Bramwell Lodge Business Cards design with a logo

I want two Business cards designed with a very modern contemporary logo UNING 1920'S FONT STYLES with the following details

Address:
Bramwell Lodge
17 Pellham Road
Helensburgh
G83 2RN

Details for card 1

Name: Dermot Ashby
email: Dermot.ashby@bramwell.lodge
Tel : +971 52 318 6094
Tel +44 7700 900 318

Details Card 2

Name: Dermot Ashby
email: Neville.osgood@bramwell.lodge
Tel : +971 52 430 9187

Bramwell lodge is a house that was built around 1880 and was used extensively in the 1920's for entertaining and parties in the arts scene, the house again will be resurrected to a modern entertainment venue

If you have any questions feel free to ask

Target Market(s)

The market for this is the young modern crowd

Industry/Entity Type

Entertainment Industry

Contact Information for Business Card

Address:
Bramwell Lodge
17 Pellham Road
Helensburgh
G83 2RN

Details for card 1

Name: Dermot Ashby
Tel : +971 52 318 6094
Tel +44 7700 900 318

Details Card 2

Name: Neville Osgood
Tel : +971 52 430 9187

Logo Text

Bramwell Lodge

Font styles to use
Other font styles liked:
• 1920'S FONT STULES

Requirements
Must have
• Modern Contemporary, whilst taking into consideration the age of the house as detailed above. YOU MUT BE USING 1920'S FONT STYLES
Nice to have
• 1920'S FONT STYLES see attached image if a suggestion
Should not have
• Should not look old or dated

```html
<!DOCTYPE html>
<html lang="en">
<head>
<meta charset="utf-8">
<title>Bramwell Lodge – Business Cards</title>
<link rel="stylesheet" href="https://fonts.googleapis.com/css2?family=Poiret+One&family=Noto+Serif:wght@400&display=swap">
<style>
  :root {
    --backdrop: #242424;
    --card: #0c0c0c;
    --card-edge: #1a1a1a;
    --gold: #d6a82a;
    --gold-soft: #b68a1e;
  }
  * { margin: 0; padding: 0; box-sizing: border-box; }
  html, body { width: 1200px; height: 900px; overflow: hidden; background: var(--backdrop); }
  .canvas { position: relative; width: 1200px; height: 900px; overflow: hidden; }

  .card {
    position: absolute;
    width: 560px;
    height: 320px;
    background: var(--card);
    border: 1px solid var(--card-edge);
    box-shadow: 0 18px 40px rgba(0,0,0,.55);
    color: var(--gold);
  }
  .card--address { left: 590px; top: 70px; }
  .card--contact { left: 50px; top: 380px; }

  .brand-name {
    font-family: "Poiret One", sans-serif;
    font-weight: 400;
    color: var(--gold);
    letter-spacing: 6px;
    text-transform: uppercase;
    white-space: nowrap;
  }
  .card .brand-name {
    position: absolute;
    left: 0; right: 0;
    text-align: center;
    font-size: 40px;
  }
  .card--address .brand-name { top: 100px; }
  .card--contact .brand-name { top: 44px; }

  .address-line {
    position: absolute;
    left: 0; right: 0; top: 190px;
    display: flex; justify-content: center; align-items: center; gap: 8px;
    font-family: "Noto Serif", serif;
    font-size: 15px;
  }

  .holder-name {
    position: absolute;
    left: 0; right: 0; top: 122px;
    text-align: center;
    font-family: "Poiret One", sans-serif;
    font-size: 30px;
    letter-spacing: 3px;
    text-transform: uppercase;
  }
  .holder-rule {
    position: absolute;
    left: 230px; top: 172px;
    width: 100px; height: 2px;
    background: var(--gold);
  }
  .contact-list {
    position: absolute;
    left: 30px; right: 30px; top: 230px;
    display: flex; flex-wrap: wrap; justify-content: center;
    gap: 12px 28px;
    list-style: none;
    font-family: "Noto Serif", serif;
    font-size: 14px;
  }
  .contact-item { display: flex; align-items: center; gap: 7px; white-space: nowrap; }
  .icon { width: 14px; height: 14px; fill: var(--gold); flex: none; }

  .brand-standalone {
    position: absolute;
    left: 730px; top: 740px;
    width: 440px;
    text-align: center;
    font-size: 40px;
  }
</style>
</head>
<body>
<main class="canvas">

  <section class="card card--address" aria-label="Business card, address side">
    <p class="brand-name">Bramwell Lodge</p>
    <p class="address-line">
      <svg class="icon" viewBox="0 0 14 14" aria-hidden="true"><path d="M7 0a4.5 4.5 0 0 0-4.5 4.5C2.5 8 7 14 7 14s4.5-6 4.5-9.5A4.5 4.5 0 0 0 7 0zm0 6.3a1.8 1.8 0 1 1 0-3.6 1.8 1.8 0 0 1 0 3.6z"/></svg>
      17 Pellham Road, Helensburgh, G83 2RN
    </p>
  </section>

  <section class="card card--contact" aria-label="Business card, contact side">
    <p class="brand-name">Bramwell Lodge</p>
    <p class="holder-name">Dermot Ashby</p>
    <div class="holder-rule"></div>
    <ul class="contact-list">
      <li class="contact-item">
        <svg class="icon" viewBox="0 0 14 14" aria-hidden="true"><path d="M1 4c0-1.5 2.5-3 6-3s6 1.5 6 3v1.2h-3V4H4v1.2H1zM3 6h8l1.5 6.5h-11zm4 1.5a2 2 0 1 0 0 4 2 2 0 0 0 0-4z"/></svg>
        +971 52 318 6094
      </li>
      <li class="contact-item">
        <svg class="icon" viewBox="0 0 14 14" aria-hidden="true"><path d="M4 0h6a1 1 0 0 1 1 1v12a1 1 0 0 1-1 1H4a1 1 0 0 1-1-1V1a1 1 0 0 1 1-1zm.5 1.5v9.5h5V1.5zM7 11.8a.7.7 0 1 0 0 1.4.7.7 0 0 0 0-1.4z"/></svg>
        +44 7700 900 318
      </li>
      <li class="contact-item">
        <svg class="icon" viewBox="0 0 14 14" aria-hidden="true"><path d="M0 2.5h14v9H0zm1.2 1.1L7 8l5.8-4.4z"/></svg>
        Dermot.ashby@bramwell.lodge
      </li>
    </ul>
  </section>

  <p class="brand-name brand-standalone">Bramwell Lodge</p>

</main>
</body>
</html>
```